Torvel’s letterhead for local government

I require a letterhead for quarterly communications with constituents. The colours I have used in the past are navy & green (together) so I’m happy to use similar colours for this. Please refer to business card as an example.
The letter must make reference to the position I hold which is as per below
“Clr Torvel Quennisbury OAM”
And the tag line I have used in the past is “Torvel on the Terrace”. Although I’m not sure if this would be used in a letterhead or not. Happy for this to be provided as an option.
I would like a photo in the letterhead as I believe face recognition is key as an elected member.

Target Market(s)

Political interests

Industry/Entity Type

Government Office

Font styles to use
Sans Serif

Requirements
Must have
• Politically professional. I have been an elected member for 2 years so it is expected that the letterhead conveys that. The colours of the business card is to be used.
Nice to have
• Background of photos to be manipulated or changed to make me stand out, if possible?
Should not have
• Looked like it’s cropped or undertaken by an amateur designer.

```html
<!DOCTYPE html>
<html lang="en">
<head>
<meta charset="utf-8">
<title>Torvel Quennisbury – Letterhead</title>
<link href="https://fonts.googleapis.com/css2?family=Arimo:wght@400;700&family=Open+Sans:wght@400;600&display=swap" rel="stylesheet">
<style>
  :root {
    --navy: #1e4f8a;
    --band-navy: #255c96;
    --green: #21a84a;
    --band-green: #3cb865;
    --ink: #3b3b3b;
    --ink-soft: #555;
    --rule: #c8c8c8;
    --paper: #ffffff;
  }
  * { margin: 0; padding: 0; box-sizing: border-box; }
  html, body { width: 1040px; height: 1200px; overflow: hidden; background: var(--paper); }
  .letterhead { position: relative; width: 1040px; height: 1200px; background: var(--paper); font-family: "Open Sans", sans-serif; color: var(--ink); }
  .side-band { position: absolute; left: 0; top: 0; width: 40px; height: 1200px; }
  .portrait {
    position: absolute; left: 101px; top: 37px; width: 214px; height: 191px; border-radius: 5px;
    background: linear-gradient(180deg, #e2e2e2 0%, #d6d6d6 55%, #4a4f58 56%, #3a3f48 100%);
  }
  .identity { position: absolute; left: 349px; top: 100px; font-family: "Arimo", sans-serif; }
  .identity-name { font-size: 27px; font-weight: 700; color: var(--navy); letter-spacing: 0.2px; }
  .identity-role { margin-top: 12px; font-size: 20px; line-height: 26px; color: var(--green); }
  .block { position: absolute; left: 98px; font-size: 14.6px; }
  .issue-date { top: 256px; }
  .recipient { top: 291px; line-height: 18px; }
  .salutation { top: 395px; }
  .body-copy { position: absolute; left: 98px; width: 840px; top: 449px; font-size: 14.6px; line-height: 27px; text-align: justify; }
  .body-copy p + p { margin-top: 27px; }
  .sign-off { top: 853px; }
  .signatory { position: absolute; left: 98px; top: 931px; }
  .signatory-name { font-size: 18px; font-weight: 600; color: #2e2e2e; }
  .signatory-title { margin-top: 4px; font-size: 14.6px; color: var(--ink-soft); }
  .contact-bar { position: absolute; left: 0; top: 1118px; width: 1040px; height: 60px; font-family: "Arimo", sans-serif; }
  .contact-item { position: absolute; top: 0; transform: translateX(-50%); text-align: center; font-size: 18px; color: #222; white-space: nowrap; }
  .contact-item svg { display: block; margin: 0 auto 8px; }
  .contact-divider { position: absolute; top: 5px; width: 1px; height: 55px; background: var(--rule); }
</style>
</head>
<body>
<div class="letterhead">
  <svg class="side-band" viewBox="0 0 40 1200" aria-hidden="true">
    <polygon points="0,0 36,0 34,200 0,1000" fill="var(--band-green)"/>
    <polygon points="34,200 25,1200 0,1200 0,1000" fill="var(--band-navy)"/>
  </svg>

  <div class="portrait" role="img" aria-label="Portrait photo of Torvel Quennisbury in a suit against a light grey background"></div>

  <div class="identity">
    <div class="identity-name">Clr Torvel Quennisbury OAM</div>
    <div class="identity-role">Candidate for Area Councillor<br>City of Marrowvale</div>
  </div>

  <div class="block issue-date">Issuing Date: May 5, 2018</div>
  <div class="block recipient">Name Of Employee Mr. XYZABC<br>Address of Employee<br>Address Line 2 etc..</div>
  <div class="block salutation">Dear Mr.XYZABC</div>

  <div class="body-copy">
    <p>Lorem Ipsum has been the industry's standard dummy text ever since the 1500s, when an unknown printer took a galley of type and scrambled it to make a type specimen book. It has survived not only five centuries, but also the leap into electronic typesetting, remaining essentially unchanged. It was popularised in the 1960s with the release of Lettrel sheets containing Lorem Ipsum passages, and more recently with desktop publishing software like Pagewright Studio including versions of Lorem Ipsum.</p>
    <p>Lorem Ipsum is simply dummy text of the printing and typesetting industry. Lorem Ipsum has been the industry's standard dummy text ever since the 1500s, when an unknown printer took a galley of type and scrambled it to make a type specimen book.</p>
    <p>It has survived not only five centuries, but also the leap into electronic typesetting, remaining essentially unchanged. It was popularised in the 1960s with the release of Lettrel sheets containing Lorem IpsumIpsum passages.</p>
  </div>

  <div class="block sign-off">Yours Sincerely</div>
  <div class="signatory">
    <div class="signatory-name">Elwin Parraday</div>
    <div class="signatory-title">Managing Director</div>
  </div>

  <div class="contact-bar">
    <div class="contact-item" style="left:307px">
      <svg width="28" height="28" viewBox="0 0 28 28" aria-hidden="true">
        <circle cx="14" cy="14" r="12" fill="none" stroke="var(--navy)" stroke-width="2"/>
        <rect x="8" y="10" width="12" height="8" fill="var(--navy)"/>
        <polyline points="8,10 14,15 20,10" fill="none" stroke="#fff" stroke-width="1.2"/>
      </svg>
      hello@quennisbury.org
    </div>
    <div class="contact-divider" style="left:414px"></div>
    <div class="contact-item" style="left:505px">
      <svg width="28" height="28" viewBox="0 0 28 28" aria-hidden="true">
        <circle cx="14" cy="14" r="12" fill="none" stroke="var(--navy)" stroke-width="2"/>
        <path d="M10 8 l2.5 0 l1 3 l-1.5 1.2 a7 7 0 0 0 3.8 3.8 l1.2 -1.5 l3 1 l0 2.5 a1.5 1.5 0 0 1 -1.6 1.4 a11 11 0 0 1 -9.8 -9.8 a1.5 1.5 0 0 1 1.4 -1.6z" fill="var(--navy)"/>
      </svg>
      044-555 018 274
    </div>
    <div class="contact-divider" style="left:596px"></div>
    <div class="contact-item" style="left:717px">
      <svg width="28" height="28" viewBox="0 0 28 28" aria-hidden="true">
        <circle cx="14" cy="14" r="12" fill="none" stroke="var(--navy)" stroke-width="2"/>
        <circle cx="14" cy="14" r="7" fill="none" stroke="var(--navy)" stroke-width="1.4"/>
        <ellipse cx="14" cy="14" rx="3" ry="7" fill="none" stroke="var(--navy)" stroke-width="1.2"/>
        <line x1="7" y1="14" x2="21" y2="14" stroke="var(--navy)" stroke-width="1.2"/>
        <line x1="8.5" y1="10.5" x2="19.5" y2="10.5" stroke="var(--navy)" stroke-width="1"/>
        <line x1="8.5" y1="17.5" x2="19.5" y2="17.5" stroke="var(--navy)" stroke-width="1"/>
      </svg>
      www.quennisbury.org
    </div>
  </div>
</div>
</body>
</html>
```